My company is throwing a party. The name is 80/20 (80% Calypso & 20% Whatever Remains)

I seek a flyer that shows this will be a very elegant, upscale event and at the same time high energy, great reggae music and dancing.

I need this flyer to be 650 pixels wide & any length, High resolution (1MB) for printing on a 4" x 6" flyer.

Target Market(s)

Fans of reggae music

Industry/Entity Type

Printing

Requirements
Must have
• Radiant Holdings Presents:
80/20
Upscale Reggae Soiree
80% Calypso - 20% Whatever Remains

Saturday May 4th, 10pm - 3am

The Lantern: 412 1/2 North Hollis Blvd, OKC

Dress to impress! We reserve the right to refuse entry

Free Entry: 1st 50 Ladies On VIP Guestlist - Discounted Early Bird Online Tickets - For Bottle Service Reservation: http://islandnight.ticketmarlo.com

More info? 405-555-0187

```html
<!DOCTYPE html>
<html lang="en">
<head>
<meta charset="utf-8">
<title>80/20 Upscale Reggae Soiree</title>
<link href="https://fonts.googleapis.com/css2?family=Bebas+Neue&family=Source+Sans+3:wght@400;600;700&family=Cormorant+Garamond:wght@500&display=swap" rel="stylesheet">
<style>
  :root {
    --ink: #0e0d0c;
    --white: #ffffff;
    --yellow: #f7e01a;
    --green: #3f9a2c;
    --red: #d3201f;
    --warm-1: #c9873f;
    --warm-2: #7a4620;
    --warm-3: #2a1a10;
    --ghost: rgba(255,255,255,0.06);
  }
  * { margin: 0; padding: 0; box-sizing: border-box; }
  html, body { width: 800px; height: 1200px; overflow: hidden; background: var(--ink); }
  .flyer {
    position: relative; width: 800px; height: 1200px; overflow: hidden;
    background: var(--ink);
    font-family: "Source Sans 3", "Helvetica Neue", Arial, sans-serif;
    color: var(--white);
  }
  .portrait-art {
    position: absolute; inset: 0 0 240px 0;
    background:
      radial-gradient(ellipse 55% 50% at 72% 35%, var(--warm-1) 0%, var(--warm-2) 45%, transparent 80%),
      radial-gradient(ellipse 40% 60% at 20% 40%, #4a3a1c 0%, transparent 75%),
      linear-gradient(180deg, var(--warm-3) 0%, #1c140d 100%);
  }
  .shade {
    position: absolute; left: 0; right: 0; bottom: 0; height: 640px;
    background: linear-gradient(180deg, transparent 0%, rgba(14,13,12,0.75) 35%, var(--ink) 60%);
  }
  .ghost-number {
    position: absolute; left: 380px; top: 600px;
    font-family: "Bebas Neue", Impact, sans-serif; font-size: 560px; line-height: 1;
    color: var(--ghost); transform: scaleX(0.72); transform-origin: left top;
    white-space: nowrap;
  }
  .brand {
    position: absolute; left: 40px; top: 44px;
    display: flex; align-items: center; gap: 14px;
  }
  .brand-dot { width: 34px; height: 34px; border-radius: 50%; background: var(--white); }
  .brand-name {
    font-family: "Cormorant Garamond", Georgia, serif; font-weight: 500;
    font-size: 30px; color: var(--white); line-height: 1;
  }
  .headline {
    position: absolute; left: 44px; top: 448px;
    font-family: "Bebas Neue", Impact, sans-serif; font-size: 300px; line-height: 0.8;
    color: var(--yellow); transform: scaleX(0.66); transform-origin: left top;
    white-space: nowrap;
  }
  .subhead {
    position: absolute; left: 40px; top: 730px;
    font-family: "Bebas Neue", Impact, sans-serif; font-size: 76px; line-height: 1;
    white-space: nowrap;
  }
  .subhead .green { color: var(--green); }
  .subhead .yellow { color: var(--yellow); }
  .subhead .red { color: var(--red); }
  .details { position: absolute; left: 40px; right: 36px; top: 830px; font-size: 26px; line-height: 1.3; }
  .details p { margin-bottom: 12px; }
  .details .accent { color: var(--yellow); font-weight: 700; }
  .details strong { font-weight: 700; }
  .details .entry { line-height: 1.45; }
  .details sup { font-size: 15px; line-height: 0; vertical-align: 9px; }
  .details .sep { color: var(--yellow); font-size: 20px; margin: 0 4px; }
  .details .url { font-style: italic; }
  .contact {
    position: absolute; left: 40px; right: 40px; top: 1122px;
    display: flex; justify-content: space-between; align-items: center; font-size: 23px;
  }
  .contact-item { display: flex; align-items: center; gap: 12px; white-space: nowrap; }
  .contact-item strong { font-weight: 700; }
  .icon { fill: var(--white); flex: none; }
</style>
</head>
<body>
<main class="flyer">
  <div class="portrait-art" role="img" aria-label="Painted close-up portrait of a reggae musician in warm amber tones"></div>
  <div class="shade"></div>
  <div class="ghost-number" aria-hidden="true">80/20</div>

  <header class="brand">
    <span class="brand-dot"></span>
    <span class="brand-name">Radiant Holdings</span>
  </header>

  <h1 class="headline">80/20</h1>
  <h2 class="subhead"><span class="green">UPSCALE</span><span class="yellow">REGGAE</span><span class="red">SOIREE</span></h2>

  <section class="details">
    <p><span class="accent">80%</span> Calypso - <span class="accent">20%</span> Whatever Remains</p>
    <p><span class="accent">Saturday May 4th</span> ♦ 10pm - 3am</p>
    <p><strong>Dress to impress!</strong> We reserve the right to refuse entry</p>
    <p class="entry"><strong>Free Entry:</strong> 1<sup>st</sup> 50 Ladies On VIP Guestlist <span class="sep">♦</span> Discounted Early Bird Online Tickets <span class="sep">♦</span> For Bottle Service Reservation: <span class="url">http://islandnight.ticketmarlo.com</span></p>
  </section>

  <footer class="contact">
    <div class="contact-item">
      <svg class="icon" width="26" height="38" viewBox="0 0 26 38" aria-hidden="true"><path d="M13 0C5.8 0 0 5.8 0 13c0 9.5 13 25 13 25s13-15.5 13-25C26 5.8 20.2 0 13 0zm0 18a5 5 0 1 1 0-10 5 5 0 0 1 0 10z"/></svg>
      <span><strong>The Lantern:</strong> 412 1/2 North Hollis Blvd, OKC</span>
    </div>
    <div class="contact-item">
      <svg class="icon" width="34" height="34" viewBox="0 0 24 24" aria-hidden="true"><path d="M6.6 10.8a15.1 15.1 0 0 0 6.6 6.6l2.2-2.2c.3-.3.7-.4 1-.2 1.1.4 2.3.6 3.6.6.6 0 1 .4 1 1V20c0 .6-.4 1-1 1C10.6 21 3 13.4 3 4c0-.6.4-1 1-1h3.5c.6 0 1 .4 1 1 0 1.3.2 2.5.6 3.6.1.3 0 .7-.2 1L6.6 10.8z"/></svg>
      <span>405-555-0187</span>
    </div>
  </footer>
</main>
</body>
</html>
```